Brookvane Consulting Business Card Design

Business Card Design for Brookvane Consulting. Brookvane Consulting is a boutique consultancy based in Atlanta, GA., that specializes in marketing strategy, organization planning, and leadership development. We provide solutions for small businesses and startups as well as Vantage 300 companies.

http://brookvaneconsulting.com/

Target Market(s)

We provide solutions for small businesses and startups as well as Vantage 300 companies.

Industry/Entity Type

Consulting

Contact Information for Business Card

Two sided business card with priority on contact information, logo, tag line (Guidance to Think Bigger, Act Sooner, Grow Stronger)

Colors

Designer to choose colors to be used in the design.

Requirements
Must have
• contact information, logo, tag line (Guidance to Think Bigger, Act Sooner, Grow Stronger)
• Simple no over communication.
Nice to have
• I would like to see different placements of logo and creative use of both sides of the card
Should not have
• Do not put too much information on the card.

```html
<!DOCTYPE html>
<html lang="en">
<head>
<meta charset="utf-8">
<title>Brookvane Consulting Business Card</title>
<link href="https://fonts.googleapis.com/css2?family=Roboto:ital,wght@0,400;0,500;1,700&display=swap" rel="stylesheet">
<style>
  :root {
    --backdrop: #3a3a3a;
    --card-dark: #3b3b3b;
    --card-light: #f2f2f2;
    --ink-dark: #2a2a2a;
    --ink-soft: #bdbdbd;
    --band: #353535;
    --band-text: #f4f4f4;
    --rule: #ffffff;
  }
  * { margin: 0; padding: 0; box-sizing: border-box; }
  html, body { width: 799px; height: 1200px; overflow: hidden; }
  body {
    background: var(--backdrop);
    font-family: "Roboto", Arial, sans-serif;
    position: relative;
  }
  .card {
    position: absolute;
    left: 80px;
    width: 640px;
    height: 366px;
    border-radius: 26px;
    overflow: hidden;
    box-shadow: 0 10px 30px rgba(0,0,0,.35);
  }
  .card--front { top: 140px; background: var(--card-dark); }
  .card--back { top: 690px; background: var(--card-light); }

  .brand {
    position: absolute;
    display: flex;
    align-items: center;
    gap: 14px;
    font-weight: 500;
    letter-spacing: 3px;
    text-transform: uppercase;
    white-space: nowrap;
  }
  .brand__mark { width: 22px; height: 22px; flex: none; }
  .card--front .brand {
    left: 0; right: 0; top: 150px;
    justify-content: center;
    font-size: 34px;
    color: var(--ink-soft);
  }
  .card--front .brand__mark { background: var(--ink-soft); }
  .card--back .brand {
    left: 50px; top: 48px;
    font-size: 30px;
    color: var(--ink-dark);
  }
  .card--back .brand__mark { background: var(--ink-dark); }

  .holder {
    position: absolute;
    left: 50px; top: 150px;
    font-size: 24px;
    font-weight: 700;
    font-style: italic;
    color: var(--ink-dark);
  }
  .contact {
    position: absolute;
    left: 330px; top: 212px;
    list-style: none;
    font-size: 17px;
    line-height: 22px;
    color: var(--ink-dark);
  }
  .band { position: absolute; left: 0; bottom: 0; width: 640px; height: 70px; }
  .tagline {
    position: absolute;
    right: 30px; bottom: 22px;
    font-size: 15px;
    line-height: 18px;
    color: var(--band-text);
    letter-spacing: .2px;
    white-space: nowrap;
  }
</style>
</head>
<body>
  <section class="card card--front" aria-label="Card front">
    <div class="brand"><span class="brand__mark"></span>Brookvane Consulting</div>
  </section>

  <section class="card card--back" aria-label="Card back">
    <div class="brand"><span class="brand__mark"></span>Brookvane Consulting</div>
    <p class="holder">Darnell</p>
    <ul class="contact">
      <li>404-555-0137</li>
      <li>darnell@brookvaneconsulting.com</li>
      <li>www.brookvaneconsulting.com</li>
    </ul>
    <svg class="band" viewBox="0 0 640 70" aria-hidden="true">
      <polygon points="0,40 200,40 225,0 640,0 640,70 0,70" fill="var(--band)"/>
      <polyline points="150,39 199,39 223,1" fill="none" stroke="var(--rule)" stroke-width="1.5"/>
    </svg>
    <p class="tagline">Guidance to Think Bigger, Act Sooner, Grow Stronger</p>
  </section>
</body>
</html>
```